Expanding National Maid Service Needs Redesign!

We need a redesigned home page for our residential cleaning company. Winner will be recognized as the designer for a brand about to go national within the United States. Winner will also become the first choice to continue working with the company to design at least 15 more pages.

Looking for redesign of homepage and redesign of logo (logo will use the same elements -- just organized differently with horizontal text).

For the design we are looking for a mix between the following websites:
www. tidyfleetcrew .example
This is our parent site that will be redesigned

www. sweeplancers .example
We really like the top/header having the three steps.
We would like to have the same font (proxima nova) and colors. We like the location and size of the booking form.
Love the section topics and would like to mimic that.

www. brightnookhelpers .example
We really like the clean art and use of colors.
We love the use of b-roll and branded images. Will provide for our website.

The perfect site would have the cleanliness, layout and booking form of Sweep Lancers and the excellent placement and use of branded images and b-roll of Bright Nook Helpers.

Link to branded images and b-roll is attached to the brief in a text file.

Please message me any questions. Good luck to everyone in the project!

Target Market(s)

Male and Female working professionals between the ages of 30-60 years old.

Industry/Entity Type

Cleaning Service

Number of Pages Required

1 page

Font styles to use
Other font styles liked:
• Proxima Nova

Colors
0355a3
add136

Requirements
Must have
• Most of this is covered in the project description.
• Would like to have our logo split up so that the art of the maids remains the same but the "Tidy Fleet Crew" text is to the right of the art. Looking for it to be a horizontal logo.
• Must use Proxima Nova font.
• Must use our branded images and videos. Feel free to create stills from the video.
Nice to have
• Nice to have, but not expected, is the b-roll edited to work with your design. We would like to see the designers vision of how the video would look with the website.
• Would be nice to have our logo given an updated look. Made horizontal as mentioned in the project description.
Should not have
• Should not feel busy. Should not use different color scheme than that of Sweep Lancers. Should not have non-branded images of maids.

```html
<!DOCTYPE html>
<html lang="en">
<head>
<meta charset="utf-8">
<title>Tidy Fleet Crew — Home Cleaning</title>
<link rel="stylesheet" href="https://fonts.googleapis.com/css2?family=Figtree:wght@400;600;700;800&display=swap">
<style>
:root{
  --blue:#0355a3;
  --green:#add136;
  --ink:#333a40;
  --muted:#7b8288;
  --line:#dfe3e6;
  --soft:#f1f2f3;
  --footer:#3d3d3d;
  --white:#ffffff;
}
*{box-sizing:border-box;margin:0;padding:0}
html,body{width:1200px;height:2224px;overflow:hidden}
body{font-family:'Figtree',sans-serif;color:var(--ink);background:var(--white);position:relative}
.abs{position:absolute}

/* header */
.site-header{left:0;top:0;width:1200px;height:72px;background:var(--white)}
.brand{left:180px;top:12px;display:flex;align-items:center;gap:10px}
.brand-dot{width:40px;height:40px;border-radius:50%;background:var(--blue)}
.brand-name{font-size:20px;font-weight:700;color:var(--blue);line-height:1}
.main-nav{right:180px;top:0;height:72px;display:flex;align-items:center;gap:30px;font-size:12px;font-weight:700;color:var(--ink);letter-spacing:.5px}
.call-btn{background:var(--green);color:var(--white);padding:9px 16px;border-radius:18px;display:flex;align-items:center;gap:6px;font-size:11px}

/* steps */
.steps{left:0;top:72px;width:1200px;height:34px;display:flex;font-size:15px;color:var(--white)}
.step{display:flex;align-items:center;gap:14px;padding-left:16px}
.step-num{font-weight:700;opacity:.9}
.step.active{background:var(--green);width:560px;padding-left:180px}
.step.next{background:#9aa1a6;flex:1;padding-left:40px}
.step.done{background:#8a9196;width:340px}

/* hero */
.hero{left:0;top:106px;width:1200px;height:784px;background:linear-gradient(120deg,#f4f5f5 0%,#e4e6e6 55%,#cfd3d4 100%)}
.hero-title{left:180px;top:150px;font-size:26px;font-weight:700;color:var(--ink)}
.hero-sub{left:180px;top:190px;font-size:15px;color:var(--ink)}
.perks{left:180px;top:228px;list-style:none;font-size:12px;line-height:1.4;color:var(--ink)}
.perks li{display:flex;gap:8px;align-items:flex-start;margin-bottom:12px}
.video{left:270px;top:390px;width:290px;height:200px;border-radius:4px;background:linear-gradient(135deg,#6d7f3a,#a7c44a 55%,#e7ecd8)}

.quote-form{left:770px;top:122px;width:232px;height:620px;background:var(--white);box-shadow:0 2px 8px rgba(0,0,0,.12);padding:20px 18px;font-size:11px}
.quote-form h2{font-size:24px;font-weight:600;color:var(--ink);margin-bottom:14px}
.quote-form label{display:block;color:var(--muted);margin:14px 0 6px}
.toggle{display:flex;height:28px;border:1px solid var(--line)}
.toggle span{flex:1;display:flex;align-items:center;justify-content:center;font-weight:600}
.toggle .on{background:var(--green);color:var(--white)}
.row{display:flex;gap:8px}
.field{flex:1;height:30px;border:1px solid var(--line);display:flex;align-items:center;justify-content:space-between;padding:0 8px;color:var(--muted);font-size:10px}
.note{color:var(--muted);font-size:9px;margin-top:6px;line-height:1.3}
.check{display:flex;align-items:center;gap:6px;margin-top:14px;color:var(--muted)}
.check i{width:10px;height:10px;border:1px solid var(--muted);display:inline-block}
.form-btn{margin-top:26px;height:36px;background:var(--blue);color:var(--white);display:flex;align-items:center;justify-content:center;font-weight:600;font-size:12px;border-radius:2px}

/* about */
.section-title{left:0;width:1200px;text-align:center;font-size:22px;font-weight:800;color:var(--ink);letter-spacing:.5px}
.about-copy{left:180px;top:1000px;width:840px;font-size:11px;line-height:1.7;color:var(--muted);text-align:center}
.about-copy p{margin-bottom:14px}
.btn{height:38px;width:140px;display:flex;align-items:center;justify-content:center;color:var(--white);font-weight:600;font-size:12px;border-radius:2px}
.btn-green{left:460px;top:1220px;background:var(--green)}
.btn-blue{left:614px;top:1220px;background:var(--blue)}

/* testimonials */
.clients{left:0;top:1370px;width:1200px;height:300px;background:var(--soft)}
.clients-sub{left:0;top:1416px;width:1200px;text-align:center;font-size:11px;color:var(--muted)}
.tcard{top:1470px;width:420px;display:flex;gap:20px;align-items:flex-start}
.avatar{width:78px;height:78px;border-radius:50%;background:linear-gradient(135deg,#c9ad95,#8c7462);flex:none}
.tcard blockquote{font-size:11px;line-height:1.6;color:var(--muted)}
.tcard cite{display:block;font-style:normal;font-size:10px;color:var(--ink);font-weight:600;margin-top:10px}
.arrow{top:1500px;font-size:22px;color:#9aa1a6}
.dots{left:0;top:1626px;width:1200px;display:flex;justify-content:center;gap:8px}
.dots i{width:7px;height:7px;border-radius:50%;background:#b9bec2}
.dots i.on{background:var(--ink)}

/* press */
.press{left:92px;top:1680px;width:1016px;display:flex;gap:16px}
.press div{flex:1;height:88px;border:1px solid var(--line);display:flex;align-items:center;justify-content:center;font-size:20px;font-weight:700;color:#4a4f54}

/* footer */
.site-footer{left:0;top:1812px;width:1200px;height:412px;background:var(--footer);color:#cfd2d4}
.f-brand{left:0;top:1860px;width:1200px;display:flex;flex-direction:column;align-items:center;gap:8px}
.f-brand .brand-dot{background:var(--white);width:48px;height:48px}
.f-brand .brand-name{color:var(--white);font-size:18px}
.social{left:0;top:1960px;width:1200px;display:flex;justify-content:center;gap:12px}
.social i{width:24px;height:24px;border-radius:50%;background:#6a6d70;display:block}
.f-nav{left:0;top:2030px;width:1200px;display:flex;justify-content:center;gap:22px;font-size:10px;font-weight:700;letter-spacing:.5px;color:#e4e6e8}
.f-legal{left:0;top:2060px;width:1200px;text-align:center;font-size:9px;line-height:1.7;color:#9ea3a7}
</style>
</head>
<body>

<header class="site-header abs">
  <div class="brand abs"><span class="brand-dot"></span><span class="brand-name">Tidy Fleet Crew</span></div>
  <nav class="main-nav abs">
    <span>FAQ</span><span>SERVICES &amp; PRICING</span><span>LOGIN</span><span>GIFT CARDS</span>
    <span class="call-btn">
      <svg width="11" height="11" viewBox="0 0 24 24"><path fill="#fff" d="M6.6 10.8a15 15 0 0 0 6.6 6.6l2.2-2.2c.3-.3.7-.4 1-.2 1.1.4 2.3.6 3.6.6.6 0 1 .4 1 1V20c0 .6-.4 1-1 1A17 17 0 0 1 3 4c0-.6.4-1 1-1h3.5c.6 0 1 .4 1 1 0 1.3.2 2.5.6 3.6.1.3 0 .7-.2 1z"/></svg>
      CALL 555-0142
    </span>
  </nav>
</header>

<div class="steps abs">
  <div class="step active"><span class="step-num">1</span>Cleaning</div>
  <div class="step next"><span class="step-num">2</span>Pricing/Availability</div>
  <div class="step done"><span class="step-num">3</span>Done!</div>
</div>

<section class="hero abs" role="img" aria-label="Bright, freshly cleaned living room with a white sofa and soft daylight"></section>
<h1 class="hero-title abs" style="top:256px">Love that feeling of a fresh, clean home?</h1>
<p class="hero-sub abs" style="top:296px">Fighting the war on dirt with eco-friendly weapons.</p>
<ul class="perks abs" style="top:334px">
  <li><svg width="12" height="12" viewBox="0 0 12 12"><path d="M1 6l3 3 7-7" stroke="#add136" stroke-width="2" fill="none"/></svg>Your friends and family will love how clean your home looks and smells!</li>
  <li><svg width="12" height="12" viewBox="0 0 12 12"><path d="M1 6l3 3 7-7" stroke="#add136" stroke-width="2" fill="none"/></svg>Let us handle the cleaning so you can have more free time.</li>
  <li><svg width="12" height="12" viewBox="0 0 12 12"><path d="M1 6l3 3 7-7" stroke="#add136" stroke-width="2" fill="none"/></svg>Tidy Fleet Crew is super flexible and affordable.</li>
  <li><svg width="12" height="12" viewBox="0 0 12 12"><path d="M1 6l3 3 7-7" stroke="#add136" stroke-width="2" fill="none"/></svg>Backed by our unique 200% Guarantee. You have nothing to lose.</li>
</ul>
<div class="video abs" style="top:498px" role="img" aria-label="Branded video still of a cleaner at work, with a play control"></div>

<form class="quote-form abs" style="top:228px">
  <h2>Get a Price</h2>
  <label>Cleaning Style</label>
  <div class="toggle"><span class="on">Flat Rate</span><span>Hourly</span></div>
  <label>Tell us about your home</label>
  <div class="row"><div class="field">2 Bedroom <span>▾</span></div><div class="field">1 Bathroom <span>▾</span></div></div>
  <p class="note">Select the options that best match your home.</p>
  <label>When would you like us to come?</label>
  <div class="field">mm/dd/yyyy</div>
  <label>Any time between</label>
  <div class="row"><div class="field">08:00 <span>▾</span></div><div class="field">12:00 <span>▾</span></div></div>
  <div class="check"><i></i>I'm Flexible</div>
  <div class="form-btn">Get a Price</div>
</form>

<h2 class="section-title abs" style="top:946px">WANT TO KNOW MORE ABOUT US?</h2>
<div class="about-copy abs">
  <p>First and foremost, Tidy Fleet Crew provides world class customer service. We don't just say that either. We want to make every single customer and home feel like a VIP. We want to help free up more of your time so you can focus on what matters most to you, whether that is family, friends, hobbies or simply resting after a long week of hard work.</p>
  <p>Most companies talk about clean, but we back it up. Every cleaner is trained, insured and background checked, and our 200% Guarantee means that if you are not happy, we will make it right, no questions asked. Give us a try today and see why so many families trust us with their homes.</p>
</div>
<a class="btn btn-green abs">Get Instant Price</a>
<a class="btn btn-blue abs">About Us</a>

<section class="clients abs"></section>
<h2 class="section-title abs" style="top:1386px">WHAT OUR CLIENTS SAY</h2>
<p class="clients-sub abs">Hear from a few of the many happy families who trust us with their homes each week.</p>
<span class="arrow abs" style="left:130px">‹</span>
<div class="tcard abs" style="left:170px">
  <div class="avatar" role="img" aria-label="Client portrait"></div>
  <blockquote>They did a wonderful job on our home. Every room was spotless and the team was friendly, on time and careful with our things. Highly recommended!<cite>Dana Whitlow</cite></blockquote>
</div>
<div class="tcard abs" style="left:610px;flex-direction:row-reverse;text-align:right">
  <div class="avatar" role="img" aria-label="Client portrait"></div>
  <blockquote>Booking was easy and the price was fair. I came home to a fresh, clean house and finally had my weekend back. We will keep using them.<cite>Mara Ellison</cite></blockquote>
</div>
<span class="arrow abs" style="left:1060px">›</span>
<div class="dots abs"><i class="on"></i><i></i><i></i></div>

<div class="press abs">
  <div>Lakeside Courier</div>
  <div>Harbor Weekly</div>
  <div>Beyond Verdant</div>
  <div>Stillmark</div>
</div>

<footer class="site-footer abs"></footer>
<div class="f-brand abs"><span class="brand-dot"></span><span class="brand-name">Tidy Fleet Crew</span></div>
<div class="social abs"><i></i><i></i><i></i></div>
<nav class="f-nav abs"><span>FAQ</span><span>BLOG</span><span>TERMS OF SERVICE</span><span>PRIVACY POLICY</span><span>JOBS</span><span>LOGIN</span><span>SITEMAP</span></nav>
<p class="f-legal abs">© 2016 Tidy Fleet Crew. All rights reserved.<br>Prices, availability and service areas may change without notice.</p>

</body>
</html>
```